Business Cards Design for the electrical wholesaler: clean bold dynamic :)

We need a business card design that would follow our latest brand guidelines. As an electrical wholesaler we want to bring a fresh look and feel into the industry. The design should be clean bold and dynamic. It should come alive with the renewed energy of our green colour. Our grey colour should keep things balanced and complement the notion of maturity and responsibility. We employ Lato as a corporate font however are not bound by this font and we’re open to interpretation here.

Target Market(s)

Electrical contractors

Industry/Entity Type

Business

Contact Information for Business Card

Logo
Name & Surname: Halyna Dorosh
Job Title: Director of Marketing
Email: halya.dorosh@quillmail.example
Cell phone: XXX.XXX.XXXX
Address: 20517 - 87 Ave. Edmonton, AB, Canada. T6K 4N8
Business Phone: 780.555.0184
Website: www.brovix.example

Font styles to use
Other font styles liked:
• Lato

Requirements
Must have
• Logo & website
Nice to have
• Brand elements - some of them you may find in the attached Brand Guidelines (e.g. three lines on the background signifying "W")

```html
<!DOCTYPE html>
<html lang="en">
<head>
<meta charset="utf-8">
<title>Brovix Business Card</title>
<link href="https://fonts.googleapis.com/css2?family=Lato:ital,wght@0,400;0,700;0,900;1,700&display=swap" rel="stylesheet">
<style>
  :root {
    --backdrop: #3a3a3a;
    --card: #262626;
    --green: #7dc242;
    --grey: #b9b9b9;
    --white: #f2f2f2;
  }
  * { margin: 0; padding: 0; box-sizing: border-box; }
  html, body { width: 799px; height: 1200px; overflow: hidden; }
  body {
    background: var(--backdrop);
    font-family: "Lato", sans-serif;
    position: relative;
  }
  .card {
    position: absolute;
    left: 80px;
    width: 640px;
    height: 366px;
    background: var(--card);
    border-radius: 24px;
    overflow: hidden;
    box-shadow: 0 10px 24px rgba(0,0,0,0.35);
  }
  .card--front { top: 110px; }
  .card--back { top: 724px; }

  .wordmark {
    display: flex;
    align-items: center;
    gap: 14px;
    color: var(--grey);
    font-weight: 700;
    line-height: 1;
  }
  .wordmark__dot {
    background: var(--green);
    border-radius: 50%;
  }
  .card--front .wordmark {
    position: absolute;
    left: 50%;
    top: 50%;
    transform: translate(-50%, -50%);
    font-size: 92px;
  }
  .card--front .wordmark__dot { width: 44px; height: 44px; }

  .accent-curve {
    position: absolute;
    left: 0;
    top: 0;
  }
  .holder {
    position: absolute;
    left: 40px;
    top: 34px;
  }
  .holder__name {
    color: var(--green);
    font-size: 26px;
    font-weight: 700;
    font-style: italic;
  }
  .holder__title {
    color: var(--white);
    font-size: 13px;
    margin-top: 2px;
  }
  .contact {
    position: absolute;
    left: 40px;
    bottom: 40px;
    color: var(--white);
    font-size: 13.5px;
    line-height: 1.45;
    list-style: none;
  }
  .contact li { display: flex; align-items: center; gap: 8px; }
  .contact .address { display: block; margin-bottom: 4px; }
  .contact svg { flex: none; }
  .card--back .wordmark {
    position: absolute;
    right: 44px;
    bottom: 44px;
    font-size: 62px;
  }
  .card--back .wordmark__dot { width: 30px; height: 30px; }
</style>
</head>
<body>

<section class="card card--front">
  <div class="wordmark"><span class="wordmark__dot"></span>brovix</div>
</section>

<section class="card card--back">
  <svg class="accent-curve" width="40" height="90" viewBox="0 0 40 90" aria-hidden="true">
    <path d="M0 0 H30 Q10 40 0 90 Z" fill="var(--green)"/>
  </svg>
  <div class="holder">
    <div class="holder__name">Halyna Dorosh</div>
    <div class="holder__title">Founder &amp; CEO</div>
  </div>
  <ul class="contact">
    <li class="address">20517 - 87 Ave. Edmonton,<br>AB, Canada. T6K 4N8</li>
    <li>
      <svg width="13" height="13" viewBox="0 0 16 16" aria-hidden="true"><circle cx="8" cy="8" r="8" fill="var(--green)"/><path d="M5 4.5c.6 3 2.6 5.6 6.5 7l.5-1.8-1.8-.8-.9.8C8 9 7 8 6.5 6.8l.8-.9-.8-1.8z" fill="var(--card)"/></svg>
      780.555.0184
    </li>
    <li>
      <svg width="13" height="13" viewBox="0 0 16 16" aria-hidden="true"><circle cx="8" cy="8" r="8" fill="var(--green)"/><rect x="4" y="5" width="8" height="6" fill="none" stroke="var(--card)" stroke-width="1.2"/><path d="M4 5l4 3.5L12 5" fill="none" stroke="var(--card)" stroke-width="1.2"/></svg>
      halya.dorosh@quillmail.example
    </li>
    <li>
      <svg width="13" height="13" viewBox="0 0 16 16" aria-hidden="true"><circle cx="8" cy="8" r="8" fill="var(--green)"/><circle cx="8" cy="8" r="4.2" fill="none" stroke="var(--card)" stroke-width="1.1"/><path d="M3.8 8h8.4M8 3.8c-2 2.5-2 5.9 0 8.4M8 3.8c2 2.5 2 5.9 0 8.4" fill="none" stroke="var(--card)" stroke-width="1"/></svg>
      www.brovix.example
    </li>
  </ul>
  <div class="wordmark"><span class="wordmark__dot"></span>brovix</div>
</section>

</body>
</html>
```